Medical "Travel" Folder for our Clients - One Side (Back and Cover)

We are seeking a cover (binder) that represents the image of our clinic and our country.

We operate primarily in the field of Occupational Health, with a strong expertise in the Maritime sector.

This cover/folder is a product that will serve as a document cover folder for safekeeping of medical documents and other documents, which our customers have to carry around the world.

* Please refer to the attachment File 2 for presentation folder specifications.

We are looking for elements related to Portugal - Lisbon and Sintra and elements related to the Maritime industry (mainly cruise ships, tankers and Oil Platforms). Samples Photos provided. Feel free to use other royal free photos.

We enclose our logo and some pictures to use (can use other material).

Would be great if you choose other photos or elements from photos, from this ones. Take in consideration Royal Free Photos.

Furthermore in order to facilitate graphic work we’re attaching a graphical guide that we will use to print the cover. We ask you to follow the instructions given by the commercial printers, please.

Information to be contemplated on the cover:
Valtoria – Núcleo de Bem-Estar Laboral, Lda
Rua Bernardino Quintela Matos Numero 7, 3ºE
2689-352 Queluz, Portugal
E-mail: geral@valtoria-exemplo.pt
www: http://www.valtoria-exemplo.pt
Telefone/Phone/Fax: +351 21 8062917
Telemóvel/Mobile: +351 938150467

Project Deadline Extended Reason: Dear PixelBazaar,As a second experience we are not happy with the result... only 3 days left and had one design submited ... Already upgraded the the value and we think is a very fair value.We would like to extend 10 days if possible. Added Tuesday, June 23, 2015

Hello Designers,Please use the template provided in the files in order for us to evaluate the designs, otherwise we will not accept it due to the printing company guidelines (also provided in the attached files) Added Friday, June 26, 2015

Thank you for all designs submitted. We will review them today.Please present all the designs with the appropriate template instead of only one page. Added Monday, June 29, 2015

Dear designers,May our description didn't provide a clear detail back and cover. We are going to print one side, with back and cover, and not 2 sides. This means that you call fill the template AREA. Added Tuesday, June 30, 2015

Project Deadline Extended Reason: Due to the confusion with the title. We want one SIDE (with back and cover) Added Tuesday, June 30, 2015

Just upgraded our Budget to get more Designs.Also upgraded the deadline.This deadline will be the final one. Added Tuesday, June 30, 2015

Industry/Entity Type

Healthcare

Colors
f37122
3176b5
85abd2

Requirements
Must have
• Only one side (use all the template area) is used/visible with the four or two colors. ( We would like to use the colors that we have in our logo, but we will accept different color shades.
• Photos - (uploaded new 2 photos)
Nice to have
• Icons can be used to identify emails, web pages, phone, etc.
• Designer can use other fonts. The ones attached refers to the logo.
• Added a few templates that we use with colourful elements that would be interesting using.
• Minimal Design.
• Portuguese Flag :)
• Can transform or convert the photos as much as you want (like using filters for instance).
• Medical Elements.
• We would like you to get as much creativity as you can be.
Should not have
• Templates different from the one provided.
• Our logo changed. However we can allow turning the logo into one or two colors (something we can use in the future as a logo redesign)

```html
<!DOCTYPE html>
<html lang="pt">
<head>
<meta charset="utf-8">
<title>Valtoria – Pasta de Documentos Médicos</title>
<link href="https://fonts.googleapis.com/css2?family=Open+Sans:wght@400;700&display=swap" rel="stylesheet">
<style>
  :root {
    --stage: #bcbdbf;
    --die: #e6e7e8;
    --paper: #ffffff;
    --orange: #f37122;
    --blue: #3176b5;
    --sky: #85abd2;
    --ink: #333333;
    --navy: #2e3a6e;
    --sea: #4f7fa8;
  }
  * { margin: 0; padding: 0; box-sizing: border-box; }
  html, body { width: 1200px; height: 928px; overflow: hidden; }
  body { background: var(--stage); font-family: "Open Sans", Arial, sans-serif; color: var(--ink); position: relative; }

  .dieline { position: absolute; left: 0; top: 0; }
  .panel { position: absolute; background: var(--paper); }
  .back-panel { left: 230px; top: 66px; width: 450px; height: 648px; overflow: hidden; }
  .cover-panel { left: 702px; top: 66px; width: 448px; height: 648px; overflow: hidden; }

  .chart-area {
    position: absolute; left: 0; top: 0; width: 450px; height: 360px;
    background: linear-gradient(180deg, #efe8d8 0%, #f3eee2 55%, rgba(255,255,255,0) 100%);
  }

  .contact-list { position: absolute; left: 0; top: 371px; width: 450px; list-style: none; text-align: center; }
  .contact-list li { height: 36.2px; font-size: 15px; line-height: 22px; display: flex; justify-content: center; align-items: flex-start; gap: 4px; }
  .contact-list svg { width: 14px; height: 14px; margin-top: 4px; fill: var(--ink); }

  .back-accents { position: absolute; left: 0; top: 468px; }

  .brand { position: absolute; left: 252px; top: 36px; display: flex; align-items: center; gap: 6px; }
  .brand-dot { width: 30px; height: 30px; border-radius: 50%; background: var(--blue); }
  .brand-name { font-size: 22px; font-weight: 700; color: var(--navy); letter-spacing: 0.5px; }

  .folder-title { position: absolute; left: 254px; top: 118px; font-size: 23px; line-height: 31px; font-weight: 400; color: var(--ink); }

  .collage { position: absolute; left: 0; top: 0; }

  .company-block { position: absolute; left: 140px; top: 495px; font-size: 16.5px; line-height: 24px; font-weight: 700; color: var(--navy); white-space: nowrap; }

  .color-bar { position: absolute; left: 0; top: 578px; width: 448px; height: 6px; display: flex; }
  .color-bar span:nth-child(1) { width: 228px; background: var(--blue); }
  .color-bar span:nth-child(2) { width: 72px; background: var(--sky); }
  .color-bar span:nth-child(3) { flex: 1; background: var(--orange); }

  .cover-caption { position: absolute; left: 0; top: 600px; width: 448px; text-align: center; font-size: 13px; color: var(--ink); }
</style>
</head>
<body>

<svg class="dieline" width="1200" height="928" viewBox="0 0 1200 928" aria-hidden="true">
  <polygon points="38,82 212,64 212,716 38,698" fill="var(--die)"/>
  <polygon points="46,90 204,74 204,706 46,690" fill="var(--paper)"/>
  <rect x="212" y="60" width="946" height="660" fill="var(--die)"/>
  <polygon points="226,716 688,716 666,906 248,906" fill="var(--die)"/>
  <polygon points="236,734 678,734 660,898 252,898" fill="var(--paper)"/>
</svg>

<section class="panel back-panel">
  <div class="chart-area" role="img" aria-label="Faded antique nautical chart of the Iberian coast with compass roses and flags"></div>

  <ul class="contact-list">
    <li><svg viewBox="0 0 14 14"><path d="M7 0a5 5 0 0 0-5 5c0 4 5 9 5 9s5-5 5-9a5 5 0 0 0-5-5zm0 7a2 2 0 1 1 0-4 2 2 0 0 1 0 4z"/></svg>2689-352 Queluz, Portugal</li>
    <li><svg viewBox="0 0 16 14"><path d="M1 5l7-5 7 5v8H1z"/><path d="M2 6l6 4 6-4" stroke="#fff" fill="none"/></svg>geral@valtoria-exemplo.pt</li>
    <li><svg viewBox="0 0 14 14"><circle cx="7" cy="7" r="6" fill="none" stroke="#333"/><ellipse cx="7" cy="7" rx="2.6" ry="6" fill="none" stroke="#333"/><path d="M1 7h12M2 4h10M2 10h10" stroke="#333"/></svg>www.valtoria-exemplo.pt</li>
    <li><svg viewBox="0 0 14 14"><circle cx="7" cy="7" r="6" fill="none" stroke="#333" stroke-width="1.4"/><path d="M5 4l2 3-1 1 2 2" stroke="#333" fill="none"/></svg><svg viewBox="0 0 14 14"><rect x="1" y="6" width="12" height="7"/><rect x="3" y="1" width="8" height="5" fill="none" stroke="#333"/></svg>+351 21 8062917</li>
    <li><svg viewBox="0 0 14 14"><rect x="3" y="2" width="8" height="12" rx="1.5"/><rect x="4.5" y="4" width="5" height="5" fill="#fff"/><path d="M9 2l2-2" stroke="#333"/></svg>+351 938150467</li>
  </ul>

  <svg class="back-accents" width="450" height="180" viewBox="0 0 450 180" aria-hidden="true">
    <polygon points="0,70 100,134 0,180" fill="var(--sky)"/>
    <polygon points="0,150 48,100 100,134 0,180" fill="var(--blue)"/>
    <polygon points="145,116 450,180 205,180" fill="var(--sky)"/>
    <polygon points="0,180 145,116 205,180" fill="var(--orange)"/>
    <polygon points="290,146 450,2 450,66 400,120" fill="var(--blue)"/>
    <polygon points="400,120 450,66 450,180" fill="var(--sky)"/>
    <polygon points="290,146 400,120 450,180" fill="var(--orange)"/>
  </svg>
</section>

<section class="panel cover-panel">
  <div class="brand">
    <span class="brand-dot"></span>
    <span class="brand-name">VALTORIA</span>
  </div>

  <h1 class="folder-title">Medicals<br>Forms<br>originals</h1>

  <svg class="collage" width="448" height="560" viewBox="0 0 448 560">
    <defs>
      <linearGradient id="lisbonScene" x1="0" y1="0" x2="0" y2="1">
        <stop offset="0" stop-color="#c9d9e6"/>
        <stop offset="0.45" stop-color="#a8b59a"/>
        <stop offset="0.7" stop-color="#6f7c5e"/>
        <stop offset="1" stop-color="#4d7aa3"/>
      </linearGradient>
      <linearGradient id="stoneScene" x1="0" y1="0" x2="0" y2="1">
        <stop offset="0" stop-color="#c7d6e3"/>
        <stop offset="1" stop-color="#b59a78"/>
      </linearGradient>
      <linearGradient id="streetScene" x1="0" y1="0" x2="0" y2="1">
        <stop offset="0" stop-color="#b9c8d4"/>
        <stop offset="1" stop-color="#d2a63a"/>
      </linearGradient>
    </defs>
    <g role="img" aria-label="Lisbon river view with suspension bridge, monument and cruise ship">
      <polygon points="32,150 113,150 356,290 356,400 160,474 32,474" fill="url(#lisbonScene)"/>
    </g>
    <polygon points="32,100 113,149 32,196" fill="var(--orange)"/>
    <g role="img" aria-label="Sintra palace and Belém tower photo fragments">
      <polygon points="302,258 358,224 358,290" fill="url(#stoneScene)"/>
      <polygon points="358,290 416,256 416,324" fill="var(--sky)"/>
      <polygon points="358,290 416,324 358,356" fill="var(--blue)"/>
      <polygon points="358,356 416,324 416,390" fill="url(#stoneScene)"/>
      <polygon points="290,370 356,330 356,432" fill="var(--sky)"/>
      <polygon points="356,370 416,400 356,432" fill="url(#stoneScene)"/>
      <polygon points="353,434 416,400 416,471" fill="var(--orange)"/>
    </g>
    <g role="img" aria-label="Lisbon tram and Pena palace photo fragments">
      <polygon points="32,392 98,430 32,470" fill="var(--blue)"/>
      <polygon points="32,470 98,430 98,510" fill="url(#streetScene)"/>
      <polygon points="32,470 98,510 32,546" fill="url(#stoneScene)"/>
      <polygon points="98,434 164,474 98,510" fill="var(--orange)"/>
    </g>
  </svg>

  <p class="company-block">Núcleo de Bem-Estar Laboral, Lda<br>- Rua Bernardino Quintela Matos<br>&nbsp;&nbsp;Numero 7, 3ºE</p>

  <div class="color-bar"><span></span><span></span><span></span></div>
  <p class="cover-caption">documentos Medicos Originais</p>
</section>

</body>
</html>
```